Website for Plumbing Company, Mr. FlowKettle

I need a 7-page fully HTML-coded website for my plumbing company, Mr. FlowKettle. We specialize in installation, repair, and replacement of both gas and electric water heaters. Although we offer both tankless (on-demand) water heaters and standard (with tank) water heaters, most of our business is related to standard (with tank) water heaters in the USA market.

These are the pages I need:
1. Home page with sections such as About Us, Our Services, Why Choose Us, Testimonials, Location Map (Palm Beach County Florida), Quote Request Form, Join Our Newsletter, Mission Statement, etc.

2. Gas Water Heaters

3. Electric Water Heaters

4. Tankless Water Heaters

5. About Us

6. Contact Us

7. Privacy Policy, Terms & Conditions

Be sure to mention the following points:
1. Same-Day Service
2. Best Price Guarantee
3. 100% Satisfaction Rating
4. 15-Year Warranty on Water Heater & Parts
5. Lifetime Warranty on Workmanship
*All Warranties are Transferrable Upon Home Sale

Once design is selected and finalized, I need the website coded in a standard HTML/CSS and temporarily hosted on your development server so I can see the website functionality that is not observable from screenshots, such as section animations, etc. Once those details are finalized, I will move the source code to my server and complete the project.

Residential Home Owners and Business Owners

Plumbing, Home Services, Remodeling, Construction

0054AA
0677BA
7BADD7
CADEEF
E8F1F8
FFC000
F8CF3A
FAE287
FDF2CF
FEFAEE
EE7325
F08F49
F5BC92
FAE3D3
FDF4ED

• Clean, colorful, and professional

```html
<!DOCTYPE html>
<html lang="en">
<head>
<meta charset="utf-8">
<title>Electric Water Heaters | Mr. FlowKettle</title>
<link href="https://fonts.googleapis.com/css2?family=Inter:wght@400;500;600;700;800&display=swap" rel="stylesheet">
<style>
:root{
  --navy:#0054AA;--blue:#0677BA;--sky:#7BADD7;--mist:#CADEEF;--ice:#E8F1F8;
  --gold:#FFC000;--gold2:#F8CF3A;--cream:#FDF2CF;--ivory:#FEFAEE;
  --orange:#EE7325;--green:#22B455;--ink:#14233B;--text:#4A5568;--line:#E3E8EF;
  --foot:#0B2E63;
}
*{box-sizing:border-box;margin:0;padding:0}
html,body{width:1200px;height:5115px;overflow:hidden}
body{font-family:"Inter",sans-serif;color:var(--ink);background:#fff;font-size:11px;line-height:1.6}
.wrap{position:relative;width:794px;margin-left:203px}
.narrow{width:507px}
h2{font-size:15px;font-weight:700;color:var(--ink)}
p{color:var(--text)}
svg{display:block}

.topbar{height:24px;background:var(--navy);color:#fff;font-size:8px;display:flex;align-items:center;padding:0 203px;gap:10px}
.topbar .pill{background:var(--gold);color:var(--ink);border-radius:10px;padding:1px 7px;font-weight:600}
.topbar .right{margin-left:auto;display:flex;gap:8px;align-items:center}
.topbar .soc{width:13px;height:13px;border-radius:50%;background:rgba(255,255,255,.25)}
.nav{height:58px;display:flex;align-items:center;padding:0 203px;border-bottom:1px solid var(--line)}
.brand{font-weight:700;font-size:11px;color:var(--navy);display:flex;align-items:center;gap:6px;white-space:nowrap}
.brand i{width:10px;height:10px;border-radius:50%;background:var(--navy);display:block}
.nav ul{list-style:none;display:flex;gap:20px;margin-left:auto;margin-right:42px;font-size:9px;font-weight:500}
.nav li.on{color:var(--navy)}
.nav li.sv{background:var(--ice);padding:2px 8px;border-radius:4px}
.btn-call{background:var(--gold);border-radius:6px;font-weight:700;font-size:10px;padding:10px 30px;display:flex;gap:6px;align-items:center}

.hero{height:415px;background:linear-gradient(100deg,var(--navy) 0%,var(--blue) 45%,#6BA9B9 68%,var(--gold2) 100%);position:relative;color:#fff}
.crumb{position:absolute;left:203px;top:52px;font-size:8px;opacity:.9}
.tag{position:absolute;left:203px;top:80px;background:var(--gold);color:var(--ink);font-size:8px;font-weight:700;border-radius:12px;padding:3px 10px}
.hero h1{position:absolute;left:203px;top:112px;font-size:29px;line-height:1.18;font-weight:800}
.hero h1 span{color:var(--gold)}
.hero .lead{position:absolute;left:203px;top:195px;width:330px;font-size:10.5px;color:#fff}
.chips{position:absolute;left:203px;top:270px;width:380px;display:flex;flex-wrap:wrap;gap:8px}
.chip{background:rgba(255,255,255,.16);border:1px solid rgba(255,255,255,.3);border-radius:12px;padding:3px 9px;font-size:8px;display:flex;gap:4px;align-items:center}
.chip b{color:var(--gold)}
.hero .ctas{position:absolute;left:203px;top:347px;display:flex;gap:12px}
.hbtn{height:48px;border-radius:6px;font-weight:700;font-size:11px;display:flex;align-items:center;justify-content:center;gap:6px;white-space:nowrap}
.hbtn.y{background:var(--gold);color:var(--ink);width:197px}
.hbtn.o{border:1.5px solid rgba(255,255,255,.8);width:158px}
.hero-media{position:absolute;left:700px;top:120px;width:300px;height:200px;border-radius:14px;background:linear-gradient(135deg,rgba(255,255,255,.18),rgba(255,255,255,.05))}
.float{position:absolute;background:#fff;color:var(--ink);border-radius:8px;box-shadow:0 8px 20px rgba(0,0,0,.15);display:flex;gap:8px;align-items:center;padding:8px 14px;font-size:7px;white-space:nowrap}
.float b{font-size:10px;display:block}
.float .bx{width:26px;height:26px;border-radius:6px;display:flex;align-items:center;justify-content:center}

.intro{padding-top:68px;font-size:10.5px;line-height:1.85}
.intro b{color:var(--ink)}
.why{margin-top:58px}
.why .sub{margin-top:8px;font-size:9.5px}
.cards{display:grid;grid-template-columns:244px 244px;gap:16px;margin-top:30px}
.card{background:#F4F7FA;border-radius:6px;height:175px;padding:22px 20px}
.card .bx{width:30px;height:30px;border-radius:6px;background:var(--mist);display:flex;align-items:center;justify-content:center}
.card h3{font-size:10.5px;margin-top:26px}
.card p{font-size:9px;margin-top:10px}
.svc{margin-top:40px}
.svc p{font-size:9.5px;margin-top:12px}
.svc ul{list-style:none;margin:8px 0 0 15px;font-size:7.5px;line-height:2.3;color:var(--text)}
.svc li b{color:var(--ink)}
.proc{margin-top:34px}
.proc h3{font-size:11px;margin-top:12px}
.proc p{font-size:9.5px;margin-top:10px}

.spec{margin-top:38px;border:1px solid var(--line);border-radius:6px;overflow:hidden}
.spec .head{background:var(--navy);color:#fff;height:40px;display:flex;align-items:center;padding:0 20px;gap:10px;font-weight:600;font-size:10px}
.spec table{width:100%;border-collapse:collapse;font-size:8px}
.spec td{height:34.4px;padding:0 20px;border-bottom:1px solid #fff}
.spec tr:nth-child(odd) td{background:#F5F7FA}
.spec td:last-child{font-weight:600;color:var(--ink)}
.spec td:first-child{color:var(--text);width:240px}

.benefits{margin-top:34px;background:#F2FAF4;border:1px solid #D6EEDC;border-radius:8px;height:300px;padding:22px 18px}
.benefits .t{display:flex;align-items:center;gap:12px;font-weight:700;font-size:12px}
.benefits .t .bx{width:28px;height:28px;border-radius:6px;background:var(--green);display:flex;align-items:center;justify-content:center}
.bgrid{display:grid;grid-template-columns:1fr 1fr;gap:14px 16px;margin-top:18px}
.bitem{display:flex;gap:8px;font-size:7.5px;line-height:1.75;color:var(--text);height:43px}
.bitem b{color:var(--ink)}
.dot{width:14px;height:14px;border-radius:50%;background:var(--green);flex:none;display:flex;align-items:center;justify-content:center}

.cmp{margin-top:34px}
.cmp p{font-size:9.5px;margin-top:12px;line-height:1.8}
.brands{font-size:8px;color:var(--text);line-height:1.55;margin-top:4px}

.pricing{position:absolute;left:0;top:2662px;width:1200px;height:696px;background:#fff;border-top:1px solid #EDF1F5}
.eyebrow{display:inline-flex;background:var(--ice);color:var(--navy);font-size:7px;font-weight:700;border-radius:10px;padding:3px 10px;letter-spacing:.5px}
.center{text-align:center}
.pricing .eyebrow{margin-top:34px}
.sec-h{font-size:22px;font-weight:800;margin-top:8px}
.sec-h span{color:var(--blue)}
.pricing .sub{font-size:10px;width:430px;margin:10px auto 0;line-height:1.8}
.plans{position:absolute;left:225px;top:156px;width:750px;display:grid;grid-template-columns:225px 255px 225px;gap:22px;align-items:start}
.plan{border-radius:8px;position:relative;background:#fff}
.plan .top{padding:26px 10px 10px;text-align:center}
.plan .size{display:inline-block;font-size:7px;font-weight:700;background:var(--ice);color:var(--navy);border-radius:8px;padding:2px 8px}
.plan h3{font-size:12px;margin-top:8px}
.plan .price{font-size:8px;color:var(--text);margin-top:4px}
.plan .price b{font-size:22px;color:var(--navy);font-weight:800}
.plan .note{font-size:7px;color:var(--text)}
.plan ul{list-style:none;padding:26px 0 0 0;font-size:7.5px;line-height:2.55;color:var(--text);text-align:left}
.plan li{display:flex;gap:6px;align-items:center}
.plan li .dot{width:11px;height:11px}
.pbtn{display:flex;align-items:center;justify-content:center;gap:6px;border:1.5px solid var(--navy);color:var(--navy);border-radius:5px;height:34px;font-size:9px;font-weight:600;width:210px;margin:42px auto 0}
.guar{font-size:7px;text-align:center;color:var(--text);margin-top:10px}
.plan.mid .top{background:var(--navy);color:#fff;border-radius:8px 8px 0 0;height:132px}
.plan.mid h3{color:#fff}
.plan.mid .size{background:none;color:#fff;padding:0}
.plan.mid .price,.plan.mid .note{color:rgba(255,255,255,.7)}
.plan.mid .price b{color:var(--gold)}
.plan.mid{border:1px solid var(--line);margin-top:-6px}
.plan.mid ul{padding-left:18px}
.plan.mid .pbtn{background:var(--gold);border:none;color:var(--ink);margin-top:20px}
.plan.mid .guar{margin-bottom:12px}
.ribbon{position:absolute;top:-8px;left:50%;transform:translateX(-50%);font-size:7px;font-weight:700;border-radius:8px;padding:2px 10px;white-space:nowrap}
.pnote{position:absolute;left:378px;top:568px;width:440px;height:76px;background:var(--ice);border-radius:6px;font-size:7.5px;text-align:center;padding:16px 24px;line-height:1.75;color:var(--text)}

.faq{position:absolute;left:0;top:3358px;width:1200px;height:544px;background:#F4F6F9}
.q{position:absolute;left:537px;width:453px;background:#fff;border-radius:6px;box-shadow:0 1px 3px rgba(0,0,0,.05);font-size:9px;font-weight:600;display:flex;align-items:center;gap:12px;padding:0 20px;height:50px}
.q .c{width:18px;height:18px;border-radius:50%;background:var(--ice);display:flex;align-items:center;justify-content:center;flex:none}
.q.open{height:114px;align-items:flex-start;flex-direction:column;gap:0;padding-top:16px}
.q.open .row{display:flex;gap:12px;align-items:center}
.q.open .c{background:var(--navy)}
.q.open p{font-weight:400;font-size:7.5px;padding-left:30px;margin-top:12px;line-height:1.85}

.other{position:absolute;left:0;top:3902px;width:1200px;height:278px}
.other .eyebrow{margin-top:48px}
.ocards{position:absolute;left:203px;top:122px;display:grid;grid-template-columns:1fr 1fr;gap:24px;width:787px}
.ocard{height:105px;border:1px solid var(--line);border-radius:6px;display:flex;overflow:hidden}
.ocard .ph{width:120px;background:linear-gradient(135deg,var(--ice),var(--mist))}
.ocard .body{flex:1;padding:14px 16px}
.ocard .bx{width:26px;height:26px;border-radius:6px;background:var(--ice);display:flex;align-items:center;justify-content:center}
.ocard h3{font-size:11px;margin-top:8px}
.ocard p{font-size:7.5px;line-height:1.6}
.ocard .arr{width:28px;background:#F4F6F9;display:flex;align-items:center;justify-content:center}

.quote{position:absolute;left:0;top:4180px;width:1200px;height:510px;background:linear-gradient(120deg,#0B3F86 0%,var(--navy) 40%,var(--blue) 75%,#4A9AD0 100%);color:#fff;overflow:hidden}
.quote .lf{position:absolute;left:203px;top:104px;width:360px}
.quote .eyebrow{background:rgba(255,255,255,.15);color:#fff}
.quote h2{color:#fff;font-size:22px;line-height:1.25;margin-top:14px;font-weight:800}
.quote h2 span{color:var(--gold)}
.quote .lf p{color:rgba(255,255,255,.85);font-size:10px;margin-top:16px;line-height:1.8}
.callbox{margin-top:20px;width:168px;height:56px;background:rgba(255,255,255,.14);border-radius:6px;display:flex;align-items:center;gap:10px;padding:0 10px;white-space:nowrap}
.callbox .bx{width:32px;height:32px;background:var(--gold);border-radius:6px;display:flex;align-items:center;justify-content:center;flex:none;color:var(--ink)}
.callbox small{font-size:7px;display:block;opacity:.8}
.callbox b{font-size:12px;white-space:nowrap}
.hours{font-size:8px;margin-top:10px;opacity:.85}
.perks{list-style:none;margin-top:20px;font-size:9px;line-height:2.3}
.perks li{display:flex;gap:8px;align-items:center}
.perks .dot{background:var(--gold);width:11px;height:11px}
.form{position:absolute;left:618px;top:50px;width:372px;height:418px;background:#fff;border-radius:10px;color:var(--ink);padding:22px 28px}
.form h3{text-align:center;font-size:12px}
.form label{display:block;font-size:7.5px;font-weight:600;margin-top:14px}
.form .two{display:grid;grid-template-columns:1fr 1fr;gap:14px}
.field{height:26px;border:1px solid var(--line);border-radius:4px;background:#F7F9FB;font-size:7.5px;color:#8A94A6;padding:0 10px;display:flex;align-items:center;margin-top:4px;justify-content:space-between}
.field.dark{color:var(--ink)}
.field.area{height:60px;align-items:flex-start;padding-top:8px}
.submit{height:34px;background:var(--gold);border-radius:5px;font-weight:700;font-size:9px;display:flex;align-items:center;justify-content:center;gap:6px;margin-top:16px}
.secure{text-align:center;font-size:7px;color:#8A94A6;margin-top:12px}
.blob{position:absolute;border-radius:50%;background:rgba(255,255,255,.07)}

.cta{position:absolute;left:0;top:4690px;width:1200px;height:138px;background:linear-gradient(100deg,var(--navy),var(--blue) 70%,#3F8ED0);overflow:hidden;color:#fff}
.cta h2{position:absolute;left:203px;top:46px;color:#fff;font-size:22px;font-weight:800;white-space:nowrap}
.cta h2 span{color:var(--gold)}
.cta .sm{position:absolute;left:203px;top:80px;font-size:9px;color:rgba(255,255,255,.35)}
.cta .b{position:absolute;top:44px;height:48px;border-radius:6px;font-weight:700;font-size:11px;display:flex;align-items:center;justify-content:center;gap:8px;white-space:nowrap}
.cta .b.y{left:641px;width:169px;background:var(--gold);color:var(--ink)}
.cta .b.o{left:823px;width:167px;border:1.5px solid rgba(255,255,255,.75)}

footer{position:absolute;left:0;top:4828px;width:1200px;height:287px;background:var(--foot);color:rgba(255,255,255,.7)}
.fcol{position:absolute;top:38px;font-size:7.5px;line-height:2.55}
.fcol h4{color:#fff;font-size:10px;margin-bottom:10px}
.fcol ul{list-style:none;padding-left:10px}
.fbrand{left:203px;width:220px}
.fbrand .brand{color:#fff}
.fbrand p{color:rgba(255,255,255,.6);font-size:7.5px;line-height:1.9;margin-top:26px}
.fsoc{display:flex;gap:10px;margin-top:18px}
.fsoc i{width:22px;height:22px;border-radius:50%;background:rgba(255,255,255,.12);display:block}
.contact li{display:flex;gap:8px;align-items:flex-start}
.contact .dot{background:var(--gold);width:9px;height:9px;margin-top:6px}
.seals{display:flex;gap:20px;margin-top:10px}
.seals div{display:flex;align-items:center;gap:6px;line-height:1.5}
.seals i{width:22px;height:22px;border-radius:4px;background:rgba(255,255,255,.18);display:block;flex:none}
.fbot{position:absolute;left:203px;right:203px;bottom:0;height:38px;border-top:1px solid rgba(255,255,255,.1);display:flex;align-items:center;font-size:7px;color:rgba(255,255,255,.5)}
.fbot span:last-child{margin-left:auto}
</style>
</head>
<body>

<div class="topbar">
  <span>&#9742; (561) XXX-XXXX</span>
  <span class="pill">&#9679; Same-Day Service Available</span>
  <div class="right"><span>&#9679; Serving Palm Beach County, FL</span><i class="soc"></i><i class="soc"></i><i class="soc"></i></div>
</div>

<header class="nav">
  <div class="brand"><i></i>Mr. FlowKettle</div>
  <ul><li class="on">Home</li><li class="sv on">Services &#8964;</li><li>About Us</li><li>Contact</li></ul>
  <div class="btn-call">
    <svg width="11" height="11" viewBox="0 0 24 24"><path fill="#14233B" d="M6.6 10.8a15 15 0 0 0 6.6 6.6l2.2-2.2c.3-.3.7-.4 1-.2 1.1.4 2.3.6 3.6.6.6 0 1 .4 1 1V20c0 .6-.4 1-1 1A17 17 0 0 1 3 4c0-.6.4-1 1-1h3.5c.6 0 1 .4 1 1 0 1.3.2 2.5.6 3.6.1.3 0 .7-.2 1z"/></svg>Call Now
  </div>
</header>

<section class="hero">
  <div class="crumb">Home &nbsp;&#8250;&nbsp; Services &nbsp;&#8250;&nbsp; Electric Water Heaters</div>
  <div class="tag">&#9889; Safe &amp; Reliable</div>
  <h1>Electric Water Heater<br><span>Installation &amp; Repair</span></h1>
  <p class="lead">Safe, reliable electric water heaters for homes without gas lines. <b>EcoRated certified</b> models with easy installation and minimal maintenance. <b>15-year warranty</b> included.</p>
  <div class="chips">
    <span class="chip"><b>&#10003;</b> No Gas Lines Required</span>
    <span class="chip"><b>&#10003;</b> 30-80 Gallon Options</span>
    <span class="chip"><b>&#10003;</b> EcoRated Certified</span>
    <span class="chip"><b>&#10003;</b> Same-Day Service</span>
  </div>
  <div class="ctas">
    <div class="hbtn y">&#9742; Call: (561) XXX-XXXX</div>
    <div class="hbtn o">&#128462; Get Free Quote</div>
  </div>
  <div class="hero-media" role="img" aria-label="Photo of an electric water heater installation"></div>
  <div class="float" style="left:575px;top:174px"><div class="bx" style="background:var(--navy)"><svg width="12" height="12" viewBox="0 0 24 24"><path fill="#fff" d="M12 2 4 5v6c0 5 3.4 9.7 8 11 4.6-1.3 8-6 8-11V5z"/></svg></div><div><b>15-Year</b>Warranty</div></div>
  <div class="float" style="left:885px;top:216px"><div class="bx" style="background:var(--green)"><svg width="12" height="12" viewBox="0 0 24 24"><path fill="#fff" d="M5 19C5 9 12 5 20 4c0 9-5 15-13 15z"/></svg></div><div><b>EcoRated</b>Certified</div></div>
</section>

<main class="wrap">
  <div class="narrow">
    <p class="intro">Electric water heaters are the <b>safest and most versatile</b> option for homeowners. They don't require gas lines, produce no combustion fumes, and are easier to install in various locations. Perfect for condos, apartments, and homes without natural gas service.</p>

    <section class="why">
      <h2>Why Choose Electric Water Heaters?</h2>
      <p class="sub">No gas lines needed, safer operation, flexible installation options, and EcoRated certified models available.</p>
      <div class="cards">
        <div class="card"><div class="bx"><svg width="12" height="12" viewBox="0 0 24 24"><path fill="#0054AA" d="M12 2 4 5v6c0 5 3.4 9.7 8 11 4.6-1.3 8-6 8-11V5z"/></svg></div><h3>Safer Operation</h3><p>No combustion, no gas leaks, no carbon monoxide risk. Electric heaters are the safest option for any home.</p></div>
        <div class="card"><div class="bx"><svg width="12" height="12" viewBox="0 0 24 24"><path fill="#0054AA" d="M12 2a7 7 0 0 0-7 7c0 5 7 13 7 13s7-8 7-13a7 7 0 0 0-7-7zm0 9.5a2.5 2.5 0 1 1 0-5 2.5 2.5 0 0 1 0 5z"/></svg></div><h3>Flexible Installation</h3><p>Install anywhere with an electrical connection. Perfect for closets, garages, or utility rooms.</p></div>
        <div class="card"><div class="bx"><svg width="12" height="12" viewBox="0 0 24 24"><path fill="#0054AA" d="M21 6.5 17.5 10 14 6.5 17.5 3a6 6 0 0 0-7.7 7.7L3 17.5 6.5 21l6.8-6.8A6 6 0 0 0 21 6.5z"/></svg></div><h3>Low Maintenance</h3><p>Fewer moving parts mean less can go wrong. Simple element replacement when needed.</p></div>
        <div class="card"><div class="bx"><svg width="12" height="12" viewBox="0 0 24 24"><path fill="#0054AA" d="M5 19C5 9 12 5 20 4c0 9-5 15-13 15z"/></svg></div><h3>Energy Efficient</h3><p>High-efficiency models qualify for EcoRated. Heat pump options save up to 50% on energy.</p></div>
      </div>
    </section>

    <section class="svc">
      <h2>Our Electric Water Heater Services</h2>
      <p>From standard tank models to high-efficiency heat pump systems, we install and service all types of electric water heaters. Our licensed technicians ensure safe, code-compliant installations every time.</p>
      <ul>
        <li><b>New Installation</b> - Complete electric water heater setup with electrical work</li>
        <li><b>Replacement</b> - Upgrade your old unit to a new, efficient model</li>
        <li><b>Repairs</b> - Element replacement, thermostat issues, leak repairs</li>
        <li><b>Maintenance</b> - Annual flush and inspection services</li>
        <li><b>Heat Pump Conversion</b> - Upgrade to hybrid heat pump technology</li>
      </ul>
    </section>

    <section class="proc">
      <h2>Our Installation Process</h2>
      <h3>Electrical Assessment</h3>
      <p>We verify your electrical panel capacity and wiring to ensure safe installation. Most homes require a 240V/30-40 amp dedicated circuit.</p>
      <h3>Right-Size Selection</h3>
      <p>We recommend the perfect capacity based on your household size, hot water usage, and space availability.</p>
      <h3>Professional Installation</h3>
      <p>Licensed electricians and plumbers work together for proper connections, code compliance, and safety.</p>
      <h3>Testing &amp; Warranty</h3>
      <p>Full system testing, temperature adjustment, usage demonstration, and complete warranty documentation.</p>
    </section>

    <section class="spec">
      <div class="head"><svg width="11" height="11" viewBox="0 0 24 24"><path fill="#fff" d="M3 5h3v3H3zm5 0h13v3H8zM3 10.5h3v3H3zm5 0h13v3H8zM3 16h3v3H3zm5 0h13v3H8z"/></svg>Electric Water Heater Specifications</div>
      <table>
        <tr><td>Tank Capacity</td><td>30, 40, 50, 65, 80 Gallons</td></tr>
        <tr><td>Power Requirements</td><td>240V / 30-40 Amp Dedicated Circuit</td></tr>
        <tr><td>Element Wattage</td><td>3,000 - 5,500 Watts</td></tr>
        <tr><td>Recovery Rate</td><td>20-25 Gallons/Hour (Standard)</td></tr>
        <tr><td>Energy Factor (UEF)</td><td>0.92-0.95 (Standard) / 2.0+ (Heat Pump)</td></tr>
        <tr><td>Manufacturer Warranty</td><td>6-12 Years (Tank)</td></tr>
        <tr><td>Our Warranty</td><td>15 Years (Parts &amp; Labor)</td></tr>
        <tr><td>Average Lifespan</td><td>12-15 Years</td></tr>
      </table>
    </section>

    <section class="benefits">
      <div class="t"><div class="bx"><svg width="12" height="12" viewBox="0 0 24 24"><path fill="none" stroke="#fff" stroke-width="3" d="m5 12 5 5 9-10"/></svg></div>Benefits of Electric Water Heaters</div>
      <div class="bgrid">
        <div class="bitem"><span class="dot"><svg width="8" height="8" viewBox="0 0 24 24"><path fill="none" stroke="#fff" stroke-width="4" d="m5 12 5 5 9-10"/></svg></span><span><b>No Gas Lines Required</b> - Install anywhere with electrical access</span></div>
        <div class="bitem"><span class="dot"><svg width="8" height="8" viewBox="0 0 24 24"><path fill="none" stroke="#fff" stroke-width="4" d="m5 12 5 5 9-10"/></svg></span><span><b>Safer Operation</b> - No combustion or carbon monoxide risk</span></div>
        <div class="bitem"><span class="dot"><svg width="8" height="8" viewBox="0 0 24 24"><path fill="none" stroke="#fff" stroke-width="4" d="m5 12 5 5 9-10"/></svg></span><span><b>Lower Upfront Cost</b> - Generally less expensive to purchase</span></div>
        <div class="bitem"><span class="dot"><svg width="8" height="8" viewBox="0 0 24 24"><path fill="none" stroke="#fff" stroke-width="4" d="m5 12 5 5 9-10"/></svg></span><span><b>Longer Lifespan</b> - 12-15 years with proper maintenance</span></div>
        <div class="bitem"><span class="dot"><svg width="8" height="8" viewBox="0 0 24 24"><path fill="none" stroke="#fff" stroke-width="4" d="m5 12 5 5 9-10"/></svg></span><span><b>EcoRated Options</b> - Heat pump models save 50%+ on energy</span></div>
        <div class="bitem"><span class="dot"><svg width="8" height="8" viewBox="0 0 24 24"><path fill="none" stroke="#fff" stroke-width="4" d="m5 12 5 5 9-10"/></svg></span><span><b>Easy Repairs</b> - Simple element and thermostat replacement</span></div>
        <div class="bitem"><span class="dot"><svg width="8" height="8" viewBox="0 0 24 24"><path fill="none" stroke="#fff" stroke-width="4" d="m5 12 5 5 9-10"/></svg></span><span><b>Quiet Operation</b> - No burner noise or pilot light</span></div>
        <div class="bitem"><span class="dot"><svg width="8" height="8" viewBox="0 0 24 24"><path fill="none" stroke="#fff" stroke-width="4" d="m5 12 5 5 9-10"/></svg></span><span><b>Consistent Temperature</b> - Precise digital thermostat control</span></div>
      </div>
    </section>

    <section class="cmp">
      <h2>Electric vs Gas Water Heaters</h2>
      <p>Wondering which is right for your home? Electric water heaters are ideal for homes without gas lines, condos with installation restrictions, or homeowners who prioritize safety. While operating costs may be slightly higher than gas, the lower purchase price, longer lifespan, and minimal maintenance often make electric the better value.</p>
    </section>
    <section class="cmp" style="margin-top:26px">
      <h2>Heat Pump Water Heaters: The Best of Both Worlds</h2>
      <p>For maximum efficiency, consider a heat pump (hybrid) water heater. These units use electricity but operate 2-3 times more efficiently than standard electric models by extracting heat from the air. In Florida's warm climate, they're an excellent choice for significant energy savings.</p>
      <p style="margin-top:8px">We Install All Major Brands</p>
      <div class="brands">Norvane<br>Calder &amp; Pike<br>Harlow Thermal<br>Quillmere<br>Kestrel</div>
    </section>
  </div>
</main>

<section class="pricing center">
  <span class="eyebrow">&#9679; PRICING</span>
  <h2 class="sec-h">Electric Water Heater <span>Packages</span></h2>
  <p class="sub">Transparent pricing with no hidden fees. All packages include installation, permits, old unit removal, and our 15-year warranty.</p>
  <div class="plans">
    <div class="plan">
      <div class="top"><span class="size">40 GALLON</span><h3>Standard Electric</h3><div class="price">Starting at <b>$1,099</b></div><div class="note">Installed same-day</div></div>
      <ul>
        <li><span class="dot"></span>40 Gallon Tank Capacity</li><li><span class="dot"></span>4,500 Watt Elements</li><li><span class="dot"></span>Ideal for 2-3 People</li><li><span class="dot"></span>6-Year Manufacturer Warranty</li><li><span class="dot"></span>Our 15-Year Warranty</li><li><span class="dot"></span>Free Old Unit Removal</li>
      </ul>
      <div class="pbtn">&#9742; Get This Package</div>
      <div class="guar">&#9679; Price Match Guarantee</div>
    </div>
    <div class="plan mid">
      <span class="ribbon" style="background:var(--gold);color:var(--ink);z-index:2">&#9733; MOST POPULAR</span>
      <div class="top"><span class="size">50 GALLON</span><h3>Premium Electric</h3><div class="price">Starting at <b>$1,399</b></div><div class="note">Best value for families</div></div>
      <ul>
        <li><span class="dot"></span>50 Gallon Tank Capacity</li><li><span class="dot"></span>4,500 Watt Elements</li><li><span class="dot"></span>Ideal for 3-5 People</li><li><span class="dot"></span>9-Year Manufacturer Warranty</li><li><span class="dot"></span>Our 15-Year Warranty</li><li><span class="dot"></span>Free Old Unit Removal</li><li><span class="dot"></span>Expansion Tank Included</li>
      </ul>
      <div class="pbtn">&#9742; Get This Package</div>
      <div class="guar">&#9679; Price Match Guarantee</div>
    </div>
    <div class="plan">
      <span class="ribbon" style="background:var(--orange);color:#fff">&#9889; ENERGY SAVER</span>
      <div class="top"><span class="size">50 GALLON</span><h3>Heat Pump Hybrid</h3><div class="price">Starting at <b>$2,999</b></div><div class="note">Save 50%+ on energy</div></div>
      <ul>
        <li><span class="dot"></span>50 Gallon Heat Pump</li><li><span class="dot"></span>3.5+ Energy Factor (UEF)</li><li><span class="dot"></span>Ideal for 3-5 People</li><li><span class="dot"></span>10-Year Manufacturer Warranty</li><li><span class="dot"></span>Our 15-Year Warranty</li><li><span class="dot"></span>Free Old Unit Removal</li><li><span class="dot"></span>Tax Credits May Apply*</li>
      </ul>
      <div class="pbtn" style="margin-top:20px">&#9742; Get This Package</div>
      <div class="guar">&#9679; Price Match Guarantee</div>
    </div>
  </div>
  <div class="pnote"><b style="color:var(--navy)">&#9432; Note:</b> Prices shown are starting prices for standard installations. Final price may vary based on electrical requirements, location, and additional parts needed. We provide exact quotes before any work begins. *Federal tax credits may apply to qualifying heat pump models.</div>
</section>

<section class="faq">
  <div class="q open" style="top:56px">
    <div class="row"><span class="c"><svg width="8" height="8" viewBox="0 0 24 24"><path fill="none" stroke="#fff" stroke-width="4" d="m5 15 7-7 7 7"/></svg></span>How long does electric water heater installation take?</div>
    <p>Most electric water heater installations are completed in <b style="color:var(--ink)">2-4 hours</b>. If electrical upgrades are needed (like a new circuit or panel work), it may take 4-6 hours. We'll provide an accurate time estimate during your free consultation.</p>
  </div>
  <div class="q" style="top:184px"><span class="c"><svg width="8" height="8" viewBox="0 0 24 24"><path fill="none" stroke="#0054AA" stroke-width="4" d="m5 9 7 7 7-7"/></svg></span>What electrical requirements do I need?</div>
  <div class="q" style="top:246px"><span class="c"><svg width="8" height="8" viewBox="0 0 24 24"><path fill="none" stroke="#0054AA" stroke-width="4" d="m5 9 7 7 7-7"/></svg></span>Is electric or gas cheaper to operate?</div>
  <div class="q" style="top:308px"><span class="c"><svg width="8" height="8" viewBox="0 0 24 24"><path fill="none" stroke="#0054AA" stroke-width="4" d="m5 9 7 7 7-7"/></svg></span>What is a heat pump water heater?</div>
  <div class="q" style="top:370px"><span class="c"><svg width="8" height="8" viewBox="0 0 24 24"><path fill="none" stroke="#0054AA" stroke-width="4" d="m5 9 7 7 7-7"/></svg></span>Why is my electric water heater not producing hot water?</div>
  <div class="q" style="top:432px"><span class="c"><svg width="8" height="8" viewBox="0 0 24 24"><path fill="none" stroke="#0054AA" stroke-width="4" d="m5 9 7 7 7-7"/></svg></span>How long do electric water heaters last?</div>
</section>

<section class="other center">
  <span class="eyebrow">&#9679; OTHER SERVICES</span>
  <h2 class="sec-h">Explore Our Other <span>Water Heater</span> Options</h2>
  <div class="ocards" style="text-align:left">
    <div class="ocard"><div class="ph" role="img" aria-label="Photo of a gas water heater"></div><div class="body"><div class="bx"><svg width="11" height="11" viewBox="0 0 24 24"><path fill="#0054AA" d="M12 2c1 4 6 6 6 12a6 6 0 0 1-12 0c0-3 2-5 3-6 0 2 1 3 2 3 0-4-1-6 1-9z"/></svg></div><h3>Gas Water Heaters</h3><p>Fast heating, lower operating costs. Perfect for larger families.</p></div><div class="arr">&#8594;</div></div>
    <div class="ocard"><div class="ph" role="img" aria-label="Photo of a tankless water heater"></div><div class="body"><div class="bx"><svg width="11" height="11" viewBox="0 0 24 24"><path fill="#0054AA" d="M4 5h16v3H4zm0 5.5h16v3H4zM4 16h16v3H4z"/></svg></div><h3>Tankless Water Heaters</h3><p>Unlimited hot water, space-saving design. Up to 40% energy savings.</p></div><div class="arr">&#8594;</div></div>
  </div>
</section>

<section class="quote">
  <i class="blob" style="width:300px;height:300px;right:-80px;top:-120px"></i>
  <i class="blob" style="width:200px;height:200px;left:-60px;bottom:-100px"></i>
  <div class="lf">
    <span class="eyebrow">&#9679; FREE QUOTE</span>
    <h2>Get Your Free <span>Electric Water Heater</span> Quote</h2>
    <p>Fill out the form and we'll get back to you within 1 hour during business hours. Or call us now for immediate assistance.</p>
    <div class="callbox"><div class="bx">&#9742;</div><div><small>Call Now</small><b>(561) XXX-XXXX</b></div></div>
    <div class="hours">&#9679; Mon-Sat: 7AM - 8PM | Sun: 8AM - 6PM</div>
    <ul class="perks"><li><span class="dot"></span>Free in-home estimates</li><li><span class="dot"></span>No pressure sales tactics</li><li><span class="dot"></span>Financing options available</li></ul>
  </div>
  <div class="form">
    <h3>Request a Quote</h3>
    <div class="two">
      <div><label>Full Name *</label><div class="field">John Smith</div></div>
      <div><label>Phone Number *</label><div class="field">(561) 123-4567</div></div>
    </div>
    <label>Email Address</label><div class="field">john@example.com</div>
    <label>Service Needed *</label><div class="field dark">Install Electric Water Heater<span>&#8964;</span></div>
    <label>Additional Details</label><div class="field area">Current tank size, age, any issues...</div>
    <div class="submit">&#10148; Submit Request</div>
    <div class="secure">&#128274; Your information is secure and will never be shared.</div>
  </div>
</section>

<section class="cta">
  <i class="blob" style="width:220px;height:220px;right:-40px;top:30px"></i>
  <h2>Need an Electric Water Heater <span>Today?</span></h2>
  <div class="sm">Same-day installation available across Palm Beach County</div>
  <div class="b y">&#9742; (561) XXX-XXXX</div>
  <div class="b o">&#128197; Schedule Online</div>
</section>

<footer>
  <div class="fcol fbrand">
    <div class="brand"><i style="background:#fff"></i>Mr. FlowKettle</div>
    <p>Palm Beach County's most trusted water heater experts. 15+ years of reliable service with industry-leading warranties.</p>
    <div class="fsoc"><i></i><i></i><i></i><i></i></div>
  </div>
  <div class="fcol" style="left:467px"><h4>Our Services</h4><ul><li>Gas Water Heaters</li><li>Electric Water Heaters</li><li>Tankless Water Heaters</li><li>Water Heater Repair</li><li>Water Heater Replacement</li></ul></div>
  <div class="fcol" style="left:652px"><h4>Quick Links</h4><ul><li>About Us</li><li>Get a Quote</li><li>Service Area</li><li>Contact Us</li><li>Privacy Policy</li></ul></div>
  <div class="fcol contact" style="left:837px;width:160px"><h4>Contact Us</h4>
    <ul style="padding-left:0"><li><span class="dot"></span>(561) XXX-XXXX</li><li><span class="dot"></span>info@mrflowkettle.com</li><li><span class="dot"></span>Palm Beach County, Florida</li><li style="line-height:1.7;margin-top:4px"><span class="dot" style="margin-top:3px"></span>Mon-Sat: 7AM-8PM | Sun: 8AM-6PM</li></ul>
    <div class="seals"><div><i></i>Licensed &amp;<br>Insured</div><div><i></i>Accredited</div></div>
  </div>
  <div class="fbot"><span>&copy; 2024 Mr. FlowKettle. All Rights Reserved.</span><span>Privacy Policy &nbsp;&nbsp;&nbsp; Terms &amp; Conditions</span></div>
</footer>

</body>
</html>
```